Business Card Design

We have recently seen two business cards that caught our attention and think the designs would work for us. We are an accounting firm that serves small businesses in a variety of industries. Attached are the two business card that inspired us along with very rough layouts. We would like to see a professional layout using our company information.

Industry/Entity Type

Accounting

Contact Information for Business Card

Company Name - Marlowe Thistle
Address - 4182 Orlanby Lane, Suite 610, Houston, TX 77093
713-555-0187 - Main
281-555-0342 - Fax

Team Member Names, emails and phone numbers (see attachment)

```html
<!DOCTYPE html>
<html lang="en">
<head>
<meta charset="utf-8">
<title>Marlowe Thistle – Business Card</title>
<link href="https://fonts.googleapis.com/css2?family=Lato:wght@400;700;900&display=swap" rel="stylesheet">
<style>
  :root {
    --stage: #e6e4e1;
    --card: #ffffff;
    --ink: #111111;
    --ink-soft: #3a3a3a;
    --muted: #8a8a8a;
    --band: #c6c6c6;
    --rule: #a9a9a9;
  }
  * { margin: 0; padding: 0; box-sizing: border-box; }
  html, body {
    width: 1200px; height: 527px; overflow: hidden;
    background: var(--stage);
    font-family: "Lato", Arial, sans-serif;
  }
  .stage {
    width: 1200px; height: 527px;
    display: flex; align-items: center; justify-content: center;
  }
  .card {
    position: relative;
    width: 700px; height: 400px;
    background: var(--card);
    box-shadow: 0 2px 10px rgba(0,0,0,.12);
    overflow: hidden;
  }
  .brand {
    position: absolute; left: 40px; top: 50px;
    width: 260px; height: 130px;
    display: flex; align-items: center; gap: 14px;
  }
  .brand-square {
    width: 30px; height: 30px; flex: none;
    background: var(--ink);
  }
  .brand-name {
    font-weight: 900; font-size: 30px; line-height: 1.05;
    color: var(--ink); letter-spacing: .5px;
  }
  .divider {
    position: absolute; left: 330px; top: 45px;
    width: 2px; height: 145px; background: var(--rule);
  }
  .contact {
    position: absolute; right: 38px; top: 50px;
    text-align: right; color: var(--ink-soft);
  }
  .contact-name {
    font-weight: 900; font-size: 21px; line-height: 1.2; letter-spacing: .3px;
    text-transform: uppercase; color: var(--ink-soft);
  }
  .contact-title {
    font-size: 13px; line-height: 1.2; color: var(--muted); margin-bottom: 8px;
  }
  .contact-line {
    display: flex; align-items: center; justify-content: flex-end;
    gap: 7px; font-size: 17px; line-height: 1.5; color: var(--ink);
  }
  .icon { width: 15px; height: 15px; flex: none; fill: var(--ink); }
  .band {
    position: absolute; left: 0; top: 218px;
    width: 100%; height: 62px; background: var(--band);
  }
  .company {
    position: absolute; left: 0; top: 218px; width: 100%; height: 62px;
    display: flex; align-items: center; justify-content: center;
    font-weight: 900; font-size: 36px; line-height: 1; letter-spacing: .5px;
    text-transform: uppercase; color: var(--ink);
  }
  .company-details {
    position: absolute; left: 0; top: 294px; width: 100%;
    text-align: center; color: var(--ink); font-size: 17px; line-height: 1.55;
  }
  .phones {
    display: flex; justify-content: center; gap: 80px;
  }
  .phones span { display: inline-flex; align-items: center; gap: 8px; }
  .web { font-weight: 700; }
</style>
</head>
<body>
<main class="stage">
  <article class="card">
    <div class="brand">
      <span class="brand-square"></span>
      <span class="brand-name">Marlowe<br>Thistle</span>
    </div>

    <div class="divider"></div>

    <section class="contact">
      <p class="contact-name">Delphine Arrowood</p>
      <p class="contact-title">Account Manager</p>
      <p class="contact-line">
        <svg class="icon" viewBox="0 0 16 16"><path d="M2 6c0-2 2-3 6-3s6 1 6 3v1h-3V5.5H5V7H2z M4 8h8l1.5 5h-11z M8 9.5a1.5 1.5 0 1 0 0 3a1.5 1.5 0 1 0 0-3z"/></svg>
        713-555-0187
      </p>
      <p class="contact-line">
        <svg class="icon" viewBox="0 0 16 16"><path d="M4 1h8v14H4z M5.5 2.5v10h5v-10z" fill-rule="evenodd"/></svg>
        832-555-0129
      </p>
      <p class="contact-line">
        <svg class="icon" viewBox="0 0 16 16"><path d="M1 3h14v10H1z M2 4.2v.6l6 4 6-4v-.6z" fill-rule="evenodd"/></svg>
        darrowood@marlowethistle.com
      </p>
    </section>

    <div class="band"></div>
    <h1 class="company">Marlowe Thistle</h1>

    <section class="company-details">
      <p>4182 Orlanby Lane, Suite 610, Houston, TX 77093</p>
      <p class="phones">
        <span>
          <svg class="icon" viewBox="0 0 16 16"><path d="M2 6c0-2 2-3 6-3s6 1 6 3v1h-3V5.5H5V7H2z M4 8h8l1.5 5h-11z"/></svg>
          713-555-0187
        </span>
        <span>
          <svg class="icon" viewBox="0 0 16 16"><path d="M4 2h7v4H4z M1 7h14v6H1z M4 10h8v5H4z"/></svg>
          281-555-0342
        </span>
      </p>
      <p class="web">www.marlowethistle.com</p>
    </section>
  </article>
</main>
</body>
</html>
```